International sports company needs packaging design for color box

We need this box for our yoga mats which we will sell online. This mat is very high quality and 100% environmentally friendly. The yoga mat comes in a stylish yoga bag that will be in the box.

Yoga enthusiasts, athletes, gymnasts, actually all people who do sporting activities and value environmental friendliness will be the contact group

The logo should be visible in any case. The creator is free to choose whether to use only the complete logo or the complete logo with the emblem. In terms of style, it should be reminiscent of a packaging box from Corvane's Vextal. Be as timeless, modern and elegant as possible. If an environmentally friendly detail can be added, this would certainly be a plus. Color should be black / white / gray.

Target Market(s)

Germany

Requirements
Must have
• Size for the color box should be 13x13x61.5 cm.

```html
<!DOCTYPE html>
<html lang="en">
<head>
<meta charset="utf-8">
<title>KARVO Yoga Mat – Box Dieline</title>
<link rel="stylesheet" href="https://fonts.googleapis.com/css2?family=Montserrat:wght@300;600;700&display=swap">
<style>
  :root {
    --backdrop: #dadada;
    --board: #ffffff;
    --ink: #111111;
    --cut-line: #b9b9b9;
    --fold-line: #c8c8c8;
    --badge-fill: #e4e4e4;
  }
  html, body {
    margin: 0;
    padding: 0;
    width: 1200px;
    height: 784px;
    overflow: hidden;
    background: var(--backdrop);
  }
  .canvas {
    position: relative;
    width: 1200px;
    height: 784px;
    background: radial-gradient(ellipse at 40% 35%, #e6e6e6 0%, var(--backdrop) 70%);
  }
  .dieline {
    position: absolute;
    left: 51px;
    top: 48px;
    width: 1098px;
    height: 687px;
  }
  .panel, .flap {
    fill: var(--board);
    stroke: var(--cut-line);
    stroke-width: 1;
  }
  .fold {
    stroke: var(--fold-line);
    stroke-width: 1;
    stroke-dasharray: 5 4;
    fill: none;
  }
  .brand-name {
    font-family: "Montserrat", sans-serif;
    font-weight: 700;
    font-size: 18px;
    letter-spacing: 2px;
    fill: var(--ink);
  }
  .brand-dot { fill: var(--ink); }
  .feature-list {
    font-family: "Montserrat", sans-serif;
    font-weight: 600;
    font-size: 8.6px;
    letter-spacing: 1.2px;
    fill: var(--ink);
  }
  .title-frame {
    fill: none;
    stroke: var(--ink);
    stroke-width: 2;
  }
  .product-title {
    font-family: "Montserrat", sans-serif;
    font-weight: 300;
    font-size: 48px;
    letter-spacing: 5px;
    fill: var(--ink);
  }
  .eco-badge {
    fill: var(--badge-fill);
  }
</style>
</head>
<body>
<main class="canvas">
  <svg class="dieline" viewBox="95 63 1046 654" xmlns="http://www.w3.org/2000/svg" aria-label="Flat dieline of the KARVO yoga mat box">

    <!-- back panel with tuck flaps -->
    <g class="row row-back">
      <path class="flap" d="M278,64 L205,72 Q185,74 185,92 L185,198 Q185,210 200,212 L278,220 Z"/>
      <path class="flap" d="M958,64 L1031,72 Q1051,74 1051,92 L1051,198 Q1051,210 1036,212 L958,220 Z"/>
      <rect class="panel" x="278" y="63" width="680" height="157"/>
      <line class="fold" x1="278" y1="63" x2="278" y2="220"/>
      <line class="fold" x1="958" y1="63" x2="958" y2="220"/>
      <g class="brand-lockup">
        <circle class="brand-dot" cx="392" cy="139" r="8"/>
        <text class="brand-name" x="410" y="146">KARVO</text>
      </g>
      <text class="feature-list">
        <tspan x="677" y="122">HIGH QUALITY YOGA MAT</tspan>
        <tspan x="677" y="144">100% ENVIRONMENTALLY FRIENDLY</tspan>
        <tspan x="677" y="165">COMES IN STYLISH YOGA BAG</tspan>
      </text>
    </g>

    <!-- title panel with end flaps -->
    <g class="row row-title">
      <path class="flap" d="M278,220 L120,220 L95,232 L95,365 L120,377 L278,377 Z"/>
      <path class="flap" d="M958,220 L1116,220 L1141,232 L1141,365 L1116,377 L958,377 Z"/>
      <line class="fold" x1="120" y1="220" x2="120" y2="377"/>
      <line class="fold" x1="1116" y1="220" x2="1116" y2="377"/>
      <rect class="panel" x="278" y="220" width="680" height="157"/>
      <line class="fold" x1="278" y1="220" x2="958" y2="220"/>
      <line class="fold" x1="278" y1="220" x2="278" y2="377"/>
      <line class="fold" x1="958" y1="220" x2="958" y2="377"/>
      <circle class="eco-badge" cx="200" cy="298" r="36" role="img" aria-label="Eco badge: yoga figure in tree pose with ring text 100% environmentally friendly, yoga mat"/>
      <rect class="title-frame" x="363" y="242" width="512" height="111"/>
      <text class="product-title" x="418" y="317">YOGA MAT</text>
      <circle class="eco-badge" cx="790" cy="298" r="38" role="img" aria-label="Eco badge: yoga figure in tree pose with ring text 100% environmentally friendly, yoga mat"/>
    </g>

    <!-- second back panel with tuck flaps -->
    <g class="row row-info">
      <path class="flap" d="M278,378 L205,387 Q185,389 185,407 L185,513 Q185,525 200,527 L278,535 Z"/>
      <path class="flap" d="M958,378 L1031,387 Q1051,389 1051,407 L1051,513 Q1051,525 1036,527 L958,535 Z"/>
      <rect class="panel" x="278" y="377" width="680" height="158"/>
      <line class="fold" x1="278" y1="377" x2="958" y2="377"/>
      <line class="fold" x1="278" y1="377" x2="278" y2="535"/>
      <line class="fold" x1="958" y1="377" x2="958" y2="535"/>
      <g class="brand-lockup">
        <circle class="brand-dot" cx="392" cy="457" r="8"/>
        <text class="brand-name" x="410" y="464">KARVO</text>
      </g>
      <text class="feature-list">
        <tspan x="677" y="440">HIGH QUALITY YOGA MAT</tspan>
        <tspan x="677" y="461">100% ENVIRONMENTALLY FRIENDLY</tspan>
        <tspan x="677" y="482">COMES IN STYLISH YOGA BAG</tspan>
      </text>
    </g>

    <!-- front panel and glue flap -->
    <g class="row row-front">
      <rect class="panel" x="278" y="535" width="680" height="157"/>
      <path class="flap" d="M278,692 L285,708 Q290,717 302,717 L934,717 Q946,717 951,708 L958,692 Z"/>
      <line class="fold" x1="278" y1="535" x2="958" y2="535"/>
      <line class="fold" x1="278" y1="692" x2="958" y2="692"/>
      <rect class="title-frame" x="363" y="557" width="512" height="111"/>
      <text class="product-title" x="418" y="632">YOGA MAT</text>
      <circle class="eco-badge" cx="790" cy="612" r="38" role="img" aria-label="Eco badge: yoga figure in tree pose with ring text 100% environmentally friendly, yoga mat"/>
    </g>
  </svg>
</main>
</body>
</html>
```